Velmora Freightway Solutions Business cards

Would like a very unique design catchy but professional for business cards. Please use log provided.Marlon WellsCeo and Founder TransCon Logistix Solutions1-888-913-3225mwells@tlsolutionsus.comwww.tlsolutionsus.com

```html
<!DOCTYPE html>
<html lang="en">
<head>
<meta charset="utf-8">
<title>Velmora Freightway Solutions – Business Cards</title>
<link rel="stylesheet" href="https://fonts.googleapis.com/css2?family=Open+Sans:wght@400;600;700&display=swap">
<style>
  :root {
    --brand-blue: #1172bd;
    --brand-red: #e8202a;
    --card-white: #ffffff;
    --backdrop: #1e1e20;
    --ink-light: #ffffff;
  }
  * { box-sizing: border-box; margin: 0; padding: 0; }
  html, body {
    width: 1200px; height: 960px; overflow: hidden;
    background: var(--backdrop);
    font-family: "Open Sans", Arial, sans-serif;
  }
  .canvas {
    position: relative; width: 1200px; height: 960px;
  }
  .card {
    position: absolute; left: 250px; width: 700px; height: 400px;
    background: var(--card-white); overflow: hidden;
  }
  .card--front { top: 50px; }
  .card--back { top: 510px; display: flex; }

  /* Front */
  .front-brand {
    position: absolute; top: 120px; left: 0; width: 100%;
    display: flex; align-items: center; justify-content: center; gap: 18px;
  }
  .front-brand__mark { width: 34px; height: 34px; background: var(--brand-red); }
  .front-brand__name {
    font-size: 40px; font-weight: 700; color: var(--brand-blue);
    letter-spacing: 0.5px; line-height: 1.15; text-align: left;
  }
  .front-url {
    position: absolute; top: 292px; left: 0; width: 100%;
    display: flex; align-items: center; justify-content: center; gap: 14px;
  }
  .front-url__rule { width: 110px; height: 2px; background: var(--brand-blue); }
  .front-url__text {
    font-size: 17px; font-weight: 600; color: #1d3f63; letter-spacing: 2px;
  }

  /* Back */
  .back-brand {
    width: 336px; height: 100%; position: relative;
    display: flex; flex-direction: column; justify-content: center; align-items: center;
    border-right: 3px solid var(--brand-red);
  }
  .back-brand__name {
    font-size: 25px; font-weight: 700; color: var(--brand-blue);
    text-align: center; line-height: 1.2; padding: 0 28px;
  }
  .back-brand__rule {
    margin-top: 14px; width: 230px; height: 2px; background: var(--brand-red);
  }
  .back-details {
    flex: 1; background: var(--brand-blue); color: var(--ink-light);
    padding: 66px 0 0 46px;
  }
  .person__name { font-size: 24px; font-weight: 700; letter-spacing: 0.5px; }
  .person__title { font-size: 19px; font-weight: 400; margin-bottom: 20px; }
  .address { font-size: 17px; line-height: 1.4; margin-bottom: 14px; }
  .contact-list { list-style: none; }
  .contact-list li {
    display: flex; align-items: center; gap: 12px;
    font-size: 17px; line-height: 1.6;
  }
  .contact-list svg { width: 15px; height: 15px; flex: none; }
</style>
</head>
<body>
<main class="canvas">
  <section class="card card--front" aria-label="Card front">
    <div class="front-brand">
      <span class="front-brand__mark"></span>
      <span class="front-brand__name">Velmora<br>Freightway Solutions</span>
    </div>
    <div class="front-url">
      <span class="front-url__rule"></span>
      <span class="front-url__text">www.vfwayroutes.com</span>
      <span class="front-url__rule"></span>
    </div>
  </section>

  <section class="card card--back" aria-label="Card back">
    <div class="back-brand">
      <p class="back-brand__name">Velmora Freightway Solutions</p>
      <span class="back-brand__rule"></span>
    </div>
    <div class="back-details">
      <p class="person__name">DORIAN PIKE</p>
      <p class="person__title">CEO AND FOUNDER</p>
      <p class="address">4410 Calder Mill Rd<br>Brookhaven, GA 30342</p>
      <ul class="contact-list">
        <li>
          <svg viewBox="0 0 16 16" aria-hidden="true"><path fill="none" stroke="#fff" stroke-width="1.6" d="M4 1.5l2.5 3-1.5 2a8 8 0 0 0 4.5 4.5l2-1.5 3 2.5-1.5 2.5C7 14 2 9 1.5 3z"/></svg>
          1-888-470-6158
        </li>
        <li>
          <svg viewBox="0 0 16 16" aria-hidden="true"><rect x="1.5" y="3.5" width="13" height="9" fill="none" stroke="#fff" stroke-width="1.6"/><path d="M1.5 3.5l6.5 5 6.5-5" fill="none" stroke="#fff" stroke-width="1.6"/></svg>
          dpike@vfwayroutes.com
        </li>
        <li>
          <svg viewBox="0 0 16 16" aria-hidden="true"><circle cx="8" cy="8" r="6.5" fill="none" stroke="#fff" stroke-width="1.4"/><ellipse cx="8" cy="8" rx="3" ry="6.5" fill="none" stroke="#fff" stroke-width="1.2"/><path d="M1.5 8h13" stroke="#fff" stroke-width="1.2"/></svg>
          www.vfwayroutes.com
        </li>
      </ul>
    </div>
  </section>
</main>
</body>
</html>
```